Provide bookkeeping and accounting services to small and growing businesses

We need website and logo design using the name Dornaby as the logo.
The target audience are small companies and startups who need:
1) Simple bookkeeping services
2) Accounting advice that only someone with many years of senior financial experience as a CPA can provide.

The services are provided by two individuals. each of whom specialize in one of the areas.

We want the website to be clean without a lot of visual distraction but don't know how to make a boring subject interesting. We believe our potential clients, small business owners, need to find what they want quickly and easily without a lot of verbiage or distractions.

We've attached a draft of the homepage and have completed the text on most of the other pages.

Target Market(s)

small and early stage growth companies in San Diego North County

Industry/Entity Type

Accounting

Number of Pages Required

1 page

Font styles to use
Sans Serif

Colors
86cfc6
33b8a4
85cae6

Requirements
Must have
• We need a design for the website homepage that includes the name Dornaby as the logo. Must include a design for the name.
• Must have color in teal or greenish blue.
Nice to have
• White background, clean, clear, uncluttered.
• We would like to use the design in a Theme on a WordPress website. Themes Paper Lantern and Quiet Harbour are appealing to us.
Should not have
• Moving pictures

```html
<!DOCTYPE html>
<html lang="en">
<head>
<meta charset="utf-8">
<title>Dornaby Accounting and Bookkeeping</title>
<link rel="stylesheet" href="https://fonts.googleapis.com/css2?family=Questrial&family=Lato:wght@400;700&display=swap">
<style>
  :root {
    --teal: #33b8a4;
    --teal-soft: #4fc2ae;
    --teal-band: #2fb39f;
    --ink: #222222;
    --text: #3a3a3a;
    --charcoal: #353535;
    --charcoal-dark: #2e2e2e;
    --rule: #bdbdbd;
    --white: #ffffff;
  }
  * { box-sizing: border-box; margin: 0; padding: 0; }
  html, body { width: 1200px; height: 2190px; overflow: hidden; }
  body { position: relative; background: var(--white); font-family: 'Lato', sans-serif; color: var(--text); }
  .abs { position: absolute; }
  .display { font-family: 'Questrial', sans-serif; font-weight: 400; }

  /* Header */
  .top-rule { left: 0; top: 0; width: 1200px; height: 4px; background: var(--teal); }
  .header { left: 0; top: 4px; width: 1200px; height: 100px; background: var(--white); }
  .brand { left: 99px; top: 16px; display: flex; align-items: center; gap: 14px; }
  .brand-square { width: 24px; height: 24px; background: var(--teal); }
  .brand-name { font-family: 'Questrial', sans-serif; font-size: 52px; line-height: 1; color: var(--teal); }
  .brand-tagline { left: 137px; top: 66px; font-family: 'Lato', sans-serif; font-size: 18px; color: var(--ink); letter-spacing: .2px; }
  .contact-line { top: 18px; display: flex; align-items: center; gap: 10px; font-size: 15px; color: var(--ink); }
  .contact-icon { width: 32px; height: 32px; border-radius: 50%; background: var(--teal-soft); display: flex; align-items: center; justify-content: center; }
  .nav { top: 66px; left: 550px; display: flex; align-items: center; }
  .nav a { font-size: 14.5px; color: var(--ink); text-decoration: none; height: 32px; line-height: 30px; padding: 0 14px; margin-right: 14px; border: 1px solid transparent; }
  .nav a.current { border-color: var(--ink); }

  /* Hero */
  .hero { left: 0; top: 104px; width: 1200px; height: 470px; background: linear-gradient(100deg, #4d7fb8 0%, #8cb1d8 28%, #e4e6ea 52%, #cfd2d6 75%, #f0f0f0 100%); }
  .hero-arrow { top: 305px; }
  .hero-caption { left: 0; top: 489px; width: 1200px; height: 85px; background: rgba(30,30,30,.55); color: var(--white); text-align: center; font-size: 29px; line-height: 34px; padding-top: 8px; }

  /* Section heads */
  .section-title { left: 0; width: 1200px; text-align: center; font-size: 38px; color: var(--ink); }
  .section-title .accent { color: var(--teal); }
  .divider { left: 321px; width: 558px; height: 1px; background: var(--rule); }
  .divider::after { content: ""; position: absolute; left: 276px; top: -3px; width: 7px; height: 7px; border-radius: 50%; background: #555; }
  .section-text { text-align: center; font-size: 15.5px; line-height: 23.5px; color: var(--ink); }
  .btn { display: flex; align-items: center; justify-content: center; font-weight: 700; font-size: 16.5px; text-decoration: none; border: 2px solid var(--teal); color: var(--teal); background: transparent; }

  /* Services */
  .service { top: 905px; width: 600px; height: 343px; color: var(--white); text-align: center; }
  .service-bookkeeping { left: 0; background: linear-gradient(135deg, #2a2a2a, #454545 55%, #3a3a3a); }
  .service-advice { left: 600px; background: linear-gradient(135deg, #45bfa9, #52c4b0 60%, #4abca8); }
  .service-icon { position: absolute; left: 271px; top: 50px; }
  .service-title { position: absolute; left: 0; top: 128px; width: 600px; font-size: 38px; }
  .service-text { position: absolute; left: 150px; top: 186px; width: 300px; font-size: 15px; line-height: 24px; }
  .service .btn { position: absolute; top: 247px; width: 173px; height: 47px; }
  .service-bookkeeping .btn { left: 237px; }
  .service-advice .btn { left: 175px; border-color: var(--charcoal-dark); color: var(--charcoal-dark); }

  /* Call band */
  .call-band { left: 0; top: 1571px; width: 1200px; height: 171px; background: var(--charcoal); }
  .dash { left: 0; width: 1200px; border-top: 2px dashed #bdbdbd; }
  .call-text { left: 96px; top: 1614px; font-size: 29px; line-height: 41px; color: var(--white); }
  .call-btn { left: 928px; top: 1632px; width: 173px; height: 47px; border: 2px solid var(--white); color: var(--white); font-size: 16px; }

  /* Map & contact */
  .map { left: 0; top: 1742px; width: 600px; height: 343px; background: linear-gradient(160deg, #e2e2e2, #d3d3d3 50%, #e6e6e6); }
  .quick { left: 600px; top: 1742px; width: 600px; height: 343px; background: linear-gradient(160deg, #4fc2ae, #5cc8b5); }
  .quick-title { left: 626px; top: 1758px; font-size: 38px; color: var(--white); }
  .field { left: 628px; width: 445px; border: 1px solid rgba(255,255,255,.9); color: var(--white); font-size: 13px; padding: 8px 14px; }
  .submit { left: 628px; top: 2025px; width: 128px; height: 34px; background: var(--white); color: var(--teal); font-weight: 700; font-size: 16px; display: flex; align-items: center; justify-content: center; }

  /* Footer */
  .footer-nav { left: 0; top: 2085px; width: 1200px; height: 61px; background: var(--charcoal-dark); }
  .footer-nav a { position: absolute; top: 22px; font-size: 13.5px; color: var(--white); text-decoration: none; letter-spacing: .3px; }
  .footer-nav a.current { color: var(--teal-soft); }
  .copyright { left: 0; top: 2146px; width: 1200px; height: 44px; background: var(--teal-band); color: var(--white); font-size: 13.5px; text-align: center; line-height: 44px; }
</style>
</head>
<body>

<div class="abs top-rule"></div>
<header class="abs header"></header>
<div class="abs brand"><span class="brand-square"></span><span class="brand-name">Dornaby</span></div>
<div class="abs brand-tagline">Accounting and Bookkeeping</div>

<div class="abs contact-line" style="left:748px">
  <span class="contact-icon"><svg width="16" height="12" viewBox="0 0 16 12"><rect x="0.5" y="0.5" width="15" height="11" fill="none" stroke="#fff" stroke-width="1.4"/><path d="M1 1l7 6 7-6" fill="none" stroke="#fff" stroke-width="1.4"/></svg></span>
  info@dornaby.com
</div>
<div class="abs contact-line" style="left:949px">
  <span class="contact-icon"><svg width="16" height="16" viewBox="0 0 24 24"><path d="M6.6 10.8a15 15 0 006.6 6.6l2.2-2.2a1 1 0 011-.25 11.4 11.4 0 003.6.57 1 1 0 011 1V20a1 1 0 01-1 1A17 17 0 013 4a1 1 0 011-1h3.5a1 1 0 011 1c0 1.25.2 2.45.57 3.57a1 1 0 01-.25 1z" fill="#fff"/></svg></span>
  +123 456 7890
</div>

<nav class="abs nav">
  <a class="current" href="#">Home</a>
  <a href="#">About Us</a>
  <a href="#">Services</a>
  <a href="#">Experience</a>
  <a href="#">Resources</a>
  <a href="#">Contact Us</a>
</nav>

<section class="abs hero" role="img" aria-label="Photo of an accountant writing on documents beside a calculator and laptop"></section>
<svg class="abs hero-arrow" style="left:40px" width="30" height="60" viewBox="0 0 30 60"><path d="M28 2L2 30l26 28" fill="none" stroke="#fff" stroke-width="2"/></svg>
<svg class="abs hero-arrow" style="left:1130px" width="30" height="60" viewBox="0 0 30 60"><path d="M2 2l26 28L2 58" fill="none" stroke="#fff" stroke-width="2"/></svg>
<div class="abs hero-caption display">Providing a full range of accounting, tax, bookkeeping<br>and business consulting services</div>

<!-- About -->
<h2 class="abs section-title display" style="top:624px">About <span class="accent">Dornaby Accounting and Bookkeeping</span></h2>
<div class="abs divider" style="top:685px"></div>
<p class="abs section-text" style="left:160px; top:706px; width:880px">Dornaby offers a flexible range of accounting and bookkeeping services and support for small and growing organizations in San Diego North County. We provide bookkeeping services specializing in LedgerLane® at your offices or remotely from ours. We also provide a broad range of accounting services or financial advice.</p>
<a class="abs btn" href="#" style="left:514px; top:796px; width:172px; height:47px">Read More</a>

<!-- Services -->
<section class="abs service service-bookkeeping" role="img" aria-label="Dark photo of a calculator keypad and pen on a ledger">
  <svg class="service-icon" width="58" height="70" viewBox="0 0 58 70">
    <rect x="1" y="1" width="56" height="68" rx="4" fill="#fff"/>
    <rect x="8" y="8" width="42" height="14" fill="#3a3a3a"/>
    <g fill="#3a3a3a">
      <rect x="8" y="28" width="10" height="8"/><rect x="24" y="28" width="10" height="8"/><rect x="40" y="28" width="10" height="8"/>
      <rect x="8" y="41" width="10" height="8"/><rect x="24" y="41" width="10" height="8"/><rect x="40" y="41" width="10" height="21"/>
      <rect x="8" y="54" width="10" height="8"/><rect x="24" y="54" width="10" height="8"/>
    </g>
  </svg>
  <h3 class="service-title display">Simple Bookkeeping</h3>
  <p class="service-text">Lorem ipsum dolor sit amet, consectetur adipiscing elit.</p>
  <a class="btn" href="#">Read More</a>
</section>
<section class="abs service service-advice" role="img" aria-label="Teal-tinted photo of financial charts and a pen">
  <svg class="service-icon" width="74" height="70" viewBox="0 0 74 70">
    <rect x="38" y="1" width="34" height="30" rx="4" fill="#fff"/>
    <path d="M44 31l-4 9 12-9z" fill="#fff"/>
    <text x="55" y="25" text-anchor="middle" font-family="Lato, sans-serif" font-weight="700" font-size="24" fill="#4abca8">$</text>
    <rect x="4" y="48" width="46" height="20" rx="8" fill="#fff"/>
    <circle cx="27" cy="34" r="11" fill="#fff"/>
  </svg>
  <h3 class="service-title display">Accounting Advice</h3>
  <p class="service-text">Lorem ipsum dolor sit amet, consectetur adipiscing elit.</p>
  <a class="btn" href="#">Read More</a>
</section>

<!-- Resources -->
<h2 class="abs section-title display" style="top:1300px">Resources</h2>
<div class="abs divider" style="top:1352px"></div>
<p class="abs section-text" style="left:175px; top:1372px; width:850px">Lorem ipsum dolor sit amet, consectetur adipiscing elit. Sed vitae magna tellus. Aenean ante nunc, semper nec cursus non, rutrum ac eros. Vestibulum mattis justo ac dui bibendum consequat a ac ipsum. Praesent a arcu venenatis, auctor velit eu, suscipit libero. Quisque convallis, leo ac pharetra sagittis.</p>
<a class="abs btn" href="#" style="left:514px; top:1463px; width:172px; height:47px">Getting Started</a>

<!-- Call band -->
<section class="abs call-band"></section>
<div class="abs dash" style="top:1578px"></div>
<div class="abs dash" style="top:1734px"></div>
<p class="abs call-text display">Lorem ipsum dolor sit amet consectetur adipiscing elit.<br>Sed vitae magna tellus aenean ante nunc.</p>
<a class="abs btn call-btn" href="#">Call Us Today</a>

<!-- Map & contact -->
<section class="abs map" role="img" aria-label="Street map showing the office location"></section>
<section class="abs quick" role="img" aria-label="Teal-tinted street map background"></section>
<h2 class="abs quick-title display">Quick Contact</h2>
<div class="abs field" style="top:1821px; height:33px">Name</div>
<div class="abs field" style="top:1872px; height:32px">Email</div>
<div class="abs field" style="top:1921px; height:85px">Message</div>
<div class="abs submit">Submit</div>

<!-- Footer -->
<nav class="abs footer-nav">
  <a class="current" href="#" style="left:183px">HOME</a>
  <a href="#" style="left:307px">ABOUT US</a>
  <a href="#" style="left:457px">SERVICES</a>
  <a href="#" style="left:602px">EXPERIENCE</a>
  <a href="#" style="left:765px">RESOURCES</a>
  <a href="#" style="left:926px">CONTACT US</a>
</nav>
<footer class="abs copyright">Copyright © 2016 Dornaby Accounting and Bookkeeping. All Rights Reserved.</footer>

</body>
</html>
```